Website for Torvel Capital - investment banking firm

We have a corporate identity (thanks to Ravinka/31842) and want to extend that into a website design.  See the attached zipped files.
We have software folks in-house to do the coding.
See the attached Project Brief & Notes for more details.  Don't worry about the actual text - lorem ipsum will be fine.
The server will be Apache.
Thank you!
Desmond

Industry/Entity Type
Investment

```html
<!DOCTYPE html>
<html lang="en">
<head>
<meta charset="utf-8">
<title>Torvel Capital – Investment Banking</title>
<link rel="stylesheet" href="https://fonts.googleapis.com/css2?family=Questrial&display=swap">
<style>
:root{
  --brand-blue:#22509c;
  --title-blue:#2a5aa8;
  --link-blue:#2a5fb8;
  --text-dark:#2b2b2b;
  --text-body:#3a3a3a;
  --band-blue:#b9d3f5;
  --panel-grey:#e6e6e6;
  --footer-bg:#1f2022;
  --footer-text:#9a9a9a;
  --white:#ffffff;
}
*{box-sizing:border-box;margin:0;padding:0}
html,body{width:760px;height:1200px;overflow:hidden;background:var(--white)}
body{font-family:"Questrial",sans-serif;color:var(--text-body)}
.page{position:relative;width:760px;height:1200px;overflow:hidden}
.abs{position:absolute}

/* header */
.site-header{left:0;top:0;width:760px;height:64px;background:var(--brand-blue)}
.brand{left:82px;top:20px;display:flex;align-items:center;gap:8px;color:var(--white);font-size:19px;letter-spacing:1px;text-transform:uppercase}
.brand-mark{width:22px;height:22px;border:2px solid var(--white);border-radius:50%}
.main-nav{left:315px;top:46px;font-size:10.5px;color:#cfdcf2;white-space:nowrap}
.main-nav a{color:#cfdcf2;text-decoration:none}
.main-nav a.active{color:var(--white)}
.main-nav .sep{margin:0 5px}

/* hero */
.hero{left:0;top:64px;width:760px;height:267px;
  background:radial-gradient(ellipse at 50% 75%,#8a5a2a 0%,#3a3530 30%,#1c1f24 65%,#121418 100%)}
.hero-caption{left:104px;top:275px;width:536px;height:48px;background:rgba(10,12,16,.72);border-left:4px solid var(--brand-blue);
  padding:6px 0 0 10px;color:var(--white);font-size:10.6px;line-height:21px;text-transform:uppercase;white-space:nowrap;overflow:hidden}
.hero-arrow{left:640px;width:19px;height:18px;background:var(--brand-blue);border:1px solid #8fb0e8}
.hero-arrow svg{display:block}

/* headings */
.section-title{font-size:14.5px;color:var(--title-blue);text-transform:uppercase;letter-spacing:.3px;font-weight:400}
.btn{display:block;background:var(--brand-blue);color:var(--white);font-size:8.5px;text-transform:uppercase;text-align:center;line-height:23px;width:68px;height:23px;box-shadow:1px 1px 2px rgba(0,0,0,.3)}

/* welcome */
.welcome-lead{left:84px;top:385px;width:300px;font-size:11.5px;line-height:14.5px;color:var(--text-dark)}
.welcome-body{left:82px;top:426px;width:292px;font-size:8.4px;line-height:14.4px}

/* featured */
.service{left:449px;width:235px;height:48px}
.service-thumb{position:absolute;left:0;top:0;width:45px;height:45px}
.service-name{position:absolute;left:53px;top:0;font-size:10.5px;color:var(--link-blue)}
.service-desc{position:absolute;left:53px;top:17px;font-size:7.9px;line-height:14px;color:var(--text-dark)}

/* global */
.world-map{left:82px;top:602px;width:171px;height:158px;background:linear-gradient(135deg,#3f7fc4 0%,#5a97d3 45%,#b9a670 70%,#3f7fc4 100%)}
.service-list{left:267px;top:612px;width:130px;list-style:none}
.service-list li{height:28.7px;border-bottom:1px solid #dcdcdc;font-size:8.3px;color:var(--link-blue);padding-top:4px}
.service-list li::before{content:"";display:inline-block;width:3px;height:3px;border-radius:50%;background:var(--link-blue);margin:0 4px 1px 0}

/* positioning */
.positioning{left:450px;top:572px;width:227px;height:188px;background:var(--panel-grey)}
.positioning .section-title{position:absolute;left:17px;top:12px}
.positioning-lead{position:absolute;left:17px;top:41px;width:200px;font-size:10.5px;line-height:14.5px;color:var(--text-dark)}
.positioning-body{position:absolute;left:17px;top:81px;width:205px;font-size:8.2px;line-height:14.4px;color:var(--text-dark)}
.positioning .btn{position:absolute;left:17px;top:151px}

/* who we are */
.who-band{left:0;top:790px;width:760px;height:211px;background:var(--band-blue)}
.who-title{left:0;top:808px;width:760px;text-align:center;font-size:14px;color:var(--title-blue);text-transform:uppercase}
.card{top:840px;width:143px;height:145px;background:var(--white);padding:11px 8px 0 8px}
.card h3{font-size:10.5px;font-weight:400;color:var(--text-dark);text-transform:uppercase;margin-bottom:12px}
.card p{font-size:8.2px;line-height:14.4px;color:var(--text-dark);height:66px}
.card a{font-size:8px;color:var(--link-blue);text-decoration:underline}

/* footer */
.site-footer{left:0;top:1030px;width:760px;height:170px;background:var(--footer-bg)}
.copyright{left:83px;top:1044px;font-size:8px;color:var(--footer-text)}
.footer-brand{left:83px;top:1076px;font-size:12px;color:var(--link-blue);text-transform:uppercase;letter-spacing:.6px}
.footer-divider{left:254px;top:1048px;width:1px;height:132px;background:#3a3b3e}
.address-title{left:288px;top:1046px;font-size:10.5px;color:var(--footer-text);text-transform:uppercase}
.address{left:289px;font-size:8px;line-height:14.4px;color:var(--footer-text)}
.offices{left:497px;top:1075px;width:175px;font-size:8px;line-height:14.4px;color:var(--footer-text)}
.email-row{left:497px;top:1154px;display:flex;align-items:center;gap:6px;font-size:8.4px;color:var(--link-blue)}
</style>
</head>
<body>
<div class="page">

  <header class="site-header abs"></header>
  <div class="brand abs"><span class="brand-mark"></span>Torvel Capital</div>
  <nav class="main-nav abs">
    <a class="active" href="#">Home</a><span class="sep">|</span><a href="#">About</a><span class="sep">|</span><a href="#">Services</a><span class="sep">|</span><a href="#">Current Engagements</a><span class="sep">|</span><a href="#">Completed Transactions</a>
  </nav>

  <div class="hero abs" role="img" aria-label="Hand touching a glowing screen of finance words such as growth, money, funds and commerce"></div>
  <div class="hero-caption abs">We are one of the largest providers of the leading investment strategies. Lorem ipsum proin<br>gravida nibh vel velit auctor aliquet. Aenean sollicitudin, lorem quis bibendum auctor,</div>
  <div class="hero-arrow abs" style="top:281px"><svg width="17" height="16" viewBox="0 0 17 16"><path d="M6 3l5 5-5 5" fill="none" stroke="#fff" stroke-width="1.5"/></svg></div>
  <div class="hero-arrow abs" style="top:301px"><svg width="17" height="16" viewBox="0 0 17 16"><path d="M11 3L6 8l5 5" fill="none" stroke="#fff" stroke-width="1.5"/></svg></div>

  <h2 class="section-title abs" style="left:83px;top:348px">Welcome to our site</h2>
  <p class="welcome-lead abs">Aenean sollicitudin, lorem quis bibendum auctor, nisi elit consequat</p>
  <p class="welcome-body abs">Lorem quis bibendum auctor, nisi elit consequat ipsum, nec sagittis sem nibh id elit. Duis sed odio sit amet nibh vulputate cursus a sit amet mauris. Morbi accumsan ipsum velit. Nam nec tellus a odio tincidunt auctor a ornare odio. Sed non &nbsp;mauris vitae erat consequat auctor eu in elit. Class aptent taciti sociosqu ad litora torquent per conubia</p>
  <a class="btn abs" style="left:83px;top:507px">Read more</a>

  <h2 class="section-title abs" style="left:448px;top:348px">Featured services</h2>
  <div class="service abs" style="top:377px">
    <div class="service-thumb" role="img" aria-label="Business team meeting photo" style="background:linear-gradient(160deg,#6f7d8c,#2f3a46)"></div>
    <div class="service-name">Aenean sollicitudin lorem quis</div>
    <div class="service-desc">Duis sed odio sit amet nibh vulputate cursus<br>a sit amet mauris. Morbi accumsan ipsum</div>
  </div>
  <div class="service abs" style="top:433px">
    <div class="service-thumb" role="img" aria-label="Businessman drawing a rising chart" style="background:linear-gradient(160deg,#e9e9e9,#8a8f96)"></div>
    <div class="service-name">Genean sollicitudin lorem quis</div>
    <div class="service-desc">Duis sed odio sit amet nibh vulputate cursus<br>a sit amet mauris. Morbi accumsan ipsum</div>
  </div>
  <div class="service abs" style="top:489px">
    <div class="service-thumb" role="img" aria-label="Advisor working at a laptop" style="background:linear-gradient(160deg,#f3f6fa,#9fb3c9)"></div>
    <div class="service-name">Tenean sollicitudin lorem quis</div>
    <div class="service-desc">Duis sed odio sit amet nibh vulputate cursus<br>a sit amet mauris. Morbi accumsan ipsum</div>
  </div>

  <h2 class="section-title abs" style="left:82px;top:574px">Global investment banking services</h2>
  <div class="world-map abs" role="img" aria-label="Map of Asia-Pacific and Australia"></div>
  <ul class="service-list abs">
    <li>Strategic Advisory Services</li>
    <li>Current Engagements</li>
    <li>Completed Transactions</li>
    <li>Regulatory Compliance</li>
  </ul>

  <section class="positioning abs">
    <h2 class="section-title">Positioning statement</h2>
    <p class="positioning-lead">Global, Professional, Trusted… or Disciplined / Effective?</p>
    <p class="positioning-body">Torvel Capital is an independent investment bank working for buyers in a number of industries. We utilize exceptional technology in finding companies to meet our client's search criteria.</p>
    <a class="btn">Read more</a>
  </section>

  <div class="who-band abs"></div>
  <h2 class="who-title abs">Who we are</h2>
  <article class="card abs" style="left:83px">
    <h3>Our name</h3>
    <p>Use the word “Torvel” – “exuberant energy” to leverage Asian–Pacific market concept.</p>
    <a>read more</a>
  </article>
  <article class="card abs" style="left:234px">
    <h3>Our clients</h3>
    <p>Torvel Capital has a diverse array of clients ranging from multi-billion dollar strategic acquirers to large private</p>
    <a>read more</a>
  </article>
  <article class="card abs" style="left:386px">
    <h3>Our process</h3>
    <p>Once we have your acquisition parameters, we feed these into our software to create an initial target list.</p>
    <a>read more</a>
  </article>
  <article class="card abs" style="left:535px">
    <h3>Team</h3>
    <p>Torvel Capital's team of bankers and advisors is comprised of experienced professionals.</p>
    <a>read more</a>
  </article>

  <footer class="site-footer abs"></footer>
  <div class="copyright abs">copyright © 2014 &nbsp;| &nbsp;Privacy Policy</div>
  <div class="footer-brand abs">Torvel Capital</div>
  <div class="footer-divider abs"></div>
  <div class="address-title abs">Address</div>
  <p class="address abs" style="top:1075px">Hong Kong: Room 1804 Harbourline Tower<br>12 - 18 Lantern Street<br>Sheung Wan, Hong Kong</p>
  <p class="address abs" style="top:1132px">Dallas: 4100 Meridian Parkway, Suite 210<br>Plano, Texas 75024</p>
  <p class="offices abs">Torvel Capital maintains offices in China, Japan, the USA and Canada. We willrespond to your enquiries rapidly. Please contact us at the email address below</p>
  <div class="email-row abs">
    <svg width="26" height="20" viewBox="0 0 26 20"><rect x="1" y="2" width="20" height="14" fill="#e8eef6" stroke="#9fb0c6"/><path d="M1 2l10 8 10-8" fill="none" stroke="#9fb0c6"/><path d="M15 14h7v-3l4 4.5-4 4.5v-3h-7z" fill="#3cae3c"/></svg>
    <span>info@torvelcapital.com</span>
  </div>

</div>
</body>
</html>
```